Business Card Design Project

Business Card
We are rebranding with a new logo
Industry/Entity Type
Business
Contact Information for Business Card
Dennis Morvale +61 487215963 dennis@quorv.com.au P.O. Box 872 Fernlow QLD 4309
Requirements
Must have
- Logo

```html
<!DOCTYPE html>
<html lang="en">
<head>
<meta charset="utf-8">
<title>Quorv International – Business Card</title>
<link rel="stylesheet" href="https://fonts.googleapis.com/css2?family=Roboto+Condensed:wght@700&family=Roboto:wght@400;500;700&display=swap">
<style>
  :root {
    --stage: #2b2b2b;
    --paper: #f4f4f4;
    --brand-blue: #1b8cc6;
    --band-light: #0aa3dc;
    --band-dark: #03506f;
    --accent-orange: #ea841f;
    --ink-light: #ffffff;
    --ink-soft: #e6f3fa;
  }
  html, body {
    margin: 0;
    width: 1200px;
    height: 960px;
    overflow: hidden;
    background: var(--stage);
  }
  .card {
    position: absolute;
    left: 407px;
    top: 143px;
    width: 386px;
    height: 675px;
    border-radius: 22px;
    overflow: hidden;
    background: var(--paper);
    font-family: "Roboto", Arial, sans-serif;
  }
  .brand {
    position: absolute;
    left: 0;
    right: 0;
    top: 0;
    height: 377px;
    display: flex;
    align-items: center;
    justify-content: center;
    gap: 14px;
  }
  .brand-mark {
    width: 34px;
    height: 34px;
    border-radius: 50%;
    background: var(--brand-blue);
    flex: none;
  }
  .brand-name {
    color: var(--brand-blue);
    font-weight: 700;
    font-size: 30px;
    line-height: 1.1;
    letter-spacing: 1px;
    text-transform: uppercase;
  }
  .contact-band {
    position: absolute;
    left: 0;
    right: 0;
    top: 377px;
    height: 258px;
    background: radial-gradient(ellipse 55% 80% at 50% 40%, var(--band-light), var(--band-dark));
    text-align: center;
    color: var(--ink-light);
  }
  .person-name {
    margin: 0;
    position: absolute;
    left: 0; right: 0;
    top: 54px;
    font-family: "Roboto Condensed", "Arial Narrow", sans-serif;
    font-weight: 700;
    font-size: 37px;
    letter-spacing: 0.5px;
    text-transform: uppercase;
  }
  .phone {
    position: absolute;
    left: 0; right: 0;
    top: 123px;
    font-weight: 500;
    font-size: 22px;
  }
  .address-block {
    position: absolute;
    left: 0; right: 0;
    top: 170px;
    font-size: 16px;
    line-height: 21px;
    color: var(--ink-soft);
  }
  .web-strip {
    position: absolute;
    left: 0;
    right: 0;
    bottom: 0;
    height: 34px;
    border-top: 6px solid var(--ink-light);
    background: var(--accent-orange);
    color: var(--ink-light);
    font-size: 16px;
    letter-spacing: 3px;
    line-height: 34px;
    text-align: center;
  }
</style>
</head>
<body>
  <main class="card">
    <header class="brand">
      <span class="brand-mark"></span>
      <span class="brand-name">Quorv<br>International</span>
    </header>
    <section class="contact-band">
      <h1 class="person-name">Dennis Morvale</h1>
      <div class="phone">+61 487215963</div>
      <div class="address-block">
        P.O. Box 872 , Fernlow QLD 4309<br>
        dennis@quorv.com.au
      </div>
    </section>
    <footer class="web-strip">www.quorv.com.au</footer>
  </main>
</body>
</html>
```